Freelance Translator in Need of a Business Card

I am a freelance Japanese to English translator. I work in the video game localization industry and do literary translation in my spare time. I would like to have both the English word 'Translator' and the Japanese '翻訳者' in the job title. The final design should evoke trust, openness, and reliability.

Target Market(s)

Video game localization companies
Japanese comic book artists

Industry/Entity Type

Business

Contact Information for Business Card

Daniel Forsvik, Translator
dan.forsvik@quellmail.net
torvenwords.com
twitter: @torven_wd

Colors

Designer to choose colors to be used in the design.

```html
<!DOCTYPE html>
<html lang="en">
<head>
<meta charset="utf-8">
<title>Torven Words — Business Card</title>
<link rel="stylesheet" href="https://fonts.googleapis.com/css2?family=Libre+Baskerville:wght@700&family=Bodoni+Moda:wght@400&display=swap">
<style>
  :root {
    --page-bg: #3d3229;
    --silver-light: #e9e6e2;
    --silver-mid: #c9c4be;
    --silver-dark: #a8a29b;
    --ink: #111111;
    --black-panel: #0c0c0c;
    --black-soft: #262626;
    --copper: #c26a2c;
    --copper-deep: #8e3a1c;
    --contact-text: #d8d4cf;
    --name-text: #bdb8b2;
  }
  html, body {
    margin: 0;
    width: 1200px;
    height: 1200px;
    overflow: hidden;
    background: var(--page-bg);
  }
  .stage {
    width: 1200px;
    height: 1200px;
    display: flex;
    align-items: center;
    justify-content: center;
  }
  .business-card {
    width: 1000px;
    height: 598px;
    display: block;
    box-shadow: 0 18px 40px rgba(0,0,0,0.45);
  }
  .brand-name {
    font-family: "Libre Baskerville", Georgia, serif;
    font-weight: 700;
    font-size: 58px;
    fill: var(--ink);
  }
  .contact-line {
    font-family: "Bodoni Moda", "Didot", serif;
    font-size: 28px;
    fill: var(--contact-text);
  }
  .person-name {
    font-family: "Bodoni Moda", "Didot", serif;
    font-size: 34px;
    fill: var(--name-text);
  }
  .person-role {
    font-family: "Bodoni Moda", "Didot", serif;
    font-size: 22px;
    fill: var(--copper-deep);
  }
</style>
</head>
<body>
<main class="stage">
  <svg class="business-card" viewBox="0 0 1070 640" xmlns="http://www.w3.org/2000/svg" aria-label="Business card of Daniel Forsvik, translator">
    <defs>
      <linearGradient id="silverSheen" x1="0" y1="0" x2="1" y2="0.4">
        <stop offset="0" stop-color="var(--silver-dark)"/>
        <stop offset="0.3" stop-color="var(--silver-light)"/>
        <stop offset="0.55" stop-color="var(--silver-mid)"/>
        <stop offset="0.8" stop-color="var(--silver-light)"/>
        <stop offset="1" stop-color="var(--silver-dark)"/>
      </linearGradient>
      <radialGradient id="panelGlow" cx="0.2" cy="0.75" r="0.7">
        <stop offset="0" stop-color="var(--black-soft)"/>
        <stop offset="1" stop-color="var(--black-panel)"/>
      </radialGradient>
    </defs>

    <!-- silver upper field -->
    <rect class="card-face" x="0" y="0" width="1070" height="640" fill="url(#silverSheen)"/>

    <!-- black lower panel -->
    <path class="lower-panel" d="M0,280 C150,360 300,400 430,392 C600,378 800,245 1070,195 L1070,640 L0,640 Z" fill="url(#panelGlow)"/>

    <!-- copper swoosh -->
    <path class="copper-swoosh" d="M0,237 C120,300 300,372 545,338 C380,368 200,335 0,275 Z" fill="var(--copper)"/>

    <!-- black swoosh -->
    <path class="ink-swoosh" d="M85,268 C250,330 420,332 570,288 C720,242 900,180 1040,178 C900,188 760,248 610,300 C455,352 250,335 85,268 Z" fill="var(--ink)"/>

    <text class="brand-name" x="115" y="165">Torven Words</text>

    <!-- contact list -->
    <g class="contact-list">
      <circle class="icon-social" cx="80" cy="462" r="11" fill="var(--copper)"/>
      <text class="contact-line" x="115" y="470">@torven_wd</text>

      <g class="icon-mail" fill="none" stroke="var(--copper)" stroke-width="2.2">
        <rect x="66" y="503" width="28" height="18" fill="var(--copper)"/>
        <path d="M66,503 L80,514 L94,503" stroke="var(--black-panel)"/>
      </g>
      <text class="contact-line" x="115" y="519">dan.forsvik@quellmail.net</text>

      <g class="icon-web">
        <circle cx="80" cy="557" r="13" fill="var(--copper)"/>
        <ellipse cx="80" cy="557" rx="5.5" ry="13" fill="none" stroke="var(--black-panel)" stroke-width="1.6"/>
        <line x1="67" y1="557" x2="93" y2="557" stroke="var(--black-panel)" stroke-width="1.6"/>
      </g>
      <text class="contact-line" x="115" y="565">www.torvenwords.com</text>
    </g>

    <!-- name block -->
    <text class="person-name" x="1000" y="472" text-anchor="end">Daniel Forsvik</text>
    <text class="person-role" x="1000" y="507" text-anchor="end">Translator 翻訳者</text>
  </svg>
</main>
</body>
</html>
```